Real Estate Brokerage Stationery Designs

I am looking to have presentation folders with business card slots on both sides along with pockets on both sides. I've attached logos, website colors along with current business card designs.

I am looking for envelope designs both big and small. Possibly new business card designs, notepad templates for big and small notepads. Letterhead designs. Pop socket designs. Realtors name badge designs.

www.brightholdrealty.example

```html
<!DOCTYPE html>
<html lang="en">
<head>
<meta charset="utf-8">
<title>Brighthold Realty – Business Card</title>
<link href="https://fonts.googleapis.com/css2?family=Roboto:wght@400;500;700&display=swap" rel="stylesheet">
<style>
  :root {
    --bg: #9c9c9c;
    --brand-blue: #0356a8;
    --paper: #ffffff;
    --band-grey: #b1b1b2;
    --photo-top: #1a64b4;
    --photo-bottom: #2b2b33;
  }
  * { margin: 0; padding: 0; box-sizing: border-box; }
  html, body { width: 1133px; height: 1200px; overflow: hidden; }
  body {
    background: var(--bg);
    font-family: "Roboto", Arial, sans-serif;
    position: relative;
  }
  .card {
    position: absolute;
    width: 696px;
    height: 398px;
    overflow: hidden;
  }
  .card--front { left: 219px; top: 153px; background: var(--paper); }
  .card--back { left: 218px; top: 647px; background: var(--brand-blue); }

  /* Front */
  .front-panel {
    position: absolute; left: 0; top: 0;
    width: 316px; height: 100%;
    background: var(--brand-blue);
    color: var(--paper);
    padding: 76px 20px 0 37px;
  }
  .agent-name { font-size: 26px; font-weight: 700; line-height: 1.1; white-space: nowrap; }
  .agent-title { font-size: 17px; font-weight: 500; margin-top: 2px; }
  .address { margin-top: 26px; font-size: 16.5px; line-height: 21px; }
  .contact-list { list-style: none; margin-top: 14px; font-size: 16.5px; }
  .contact-list li { display: flex; align-items: center; height: 22px; white-space: nowrap; }
  .contact-list svg { width: 16px; height: 16px; margin-right: 12px; flex: none; fill: var(--paper); }

  .brand-area {
    position: absolute; left: 316px; top: 0; right: 0; height: 332px;
    display: flex; align-items: center; justify-content: center; gap: 12px;
  }
  .brand-mark { width: 22px; height: 22px; background: var(--brand-blue); }
  .brand-name { font-size: 34px; font-weight: 700; color: var(--brand-blue); }
  .web-band {
    position: absolute; left: 316px; right: 0; top: 332px; height: 32px;
    background: var(--band-grey);
    color: var(--paper);
    display: flex; align-items: center; justify-content: center;
    font-size: 13px; letter-spacing: 3.5px;
  }

  /* Back */
  .portrait {
    position: absolute; left: 0; top: 26px; width: 335px; bottom: 0;
    background: linear-gradient(180deg, var(--photo-top) 0%, var(--photo-top) 50%, var(--photo-bottom) 100%);
  }
  .badges { position: absolute; right: 31px; top: 33px; display: flex; gap: 8px; align-items: center; }
  .badge-house { width: 52px; height: 44px; border: 2px solid var(--paper); }
  .badge-listing { width: 84px; height: 40px; border: 1.5px solid var(--paper); }
  .back-brand {
    position: absolute; right: 31px; top: 205px;
    font-size: 40px; font-weight: 700; color: var(--paper);
  }
  .services {
    position: absolute; right: 31px; top: 300px;
    list-style: none; text-align: right; color: var(--paper);
    font-size: 17px; line-height: 21px; white-space: nowrap;
  }
  .services .dot {
    display: inline-block; width: 6px; height: 6px; background: var(--paper);
    margin: 0 0 2px 9px; vertical-align: middle;
  }
  .services .dot--between { margin: 0 5px 2px 5px; }
</style>
</head>
<body>

<section class="card card--front">
  <div class="front-panel">
    <h1 class="agent-name">Marcus Delorme</h1>
    <p class="agent-title">Broker</p>
    <p class="address">2400 Harbor Point Blvd<br>Suite 310,<br>Lakeview Shores, FL 33990</p>
    <ul class="contact-list">
      <li><svg viewBox="0 0 16 16"><path d="M3.5 1l2.5 3-1.5 1.8c.9 2 2.6 3.7 4.7 4.7L11 9l3 2.5-1.5 2.8C7 14 2 9 1.7 3z"/></svg>555-201-4830</li>
      <li><svg viewBox="0 0 16 16"><path d="M4 0h8v16H4zM5.5 1.5v11h5v-11z"/></svg>555-201-7712</li>
      <li><svg viewBox="0 0 16 16"><path d="M4 1h8v4H4zM1 6h14v7h-2v-2H3v2H1zM3 12h10v3H3z"/></svg>555-201-9064</li>
      <li><svg viewBox="0 0 16 16"><path d="M1 3h14v10H1zM2.5 4.5L8 9l5.5-4.5z" fill-rule="evenodd"/></svg>marcus@brighthold.example</li>
    </ul>
  </div>
  <div class="brand-area">
    <span class="brand-mark"></span>
    <span class="brand-name">Brighthold Realty</span>
  </div>
  <div class="web-band">www.brightholdrealty.example</div>
</section>

<section class="card card--back">
  <div class="portrait" role="img" aria-label="Portrait photograph of the broker in a dark suit and tie"></div>
  <div class="badges">
    <span class="badge-house"></span>
    <span class="badge-listing"></span>
  </div>
  <p class="back-brand">Brighthold Realty</p>
  <ul class="services">
    <li>Esidential Real Estate<span class="dot"></span></li>
    <li>CommercialReal Estate<span class="dot"></span></li>
    <li>Property Management<span class="dot dot--between"></span>Investments<span class="dot"></span></li>
  </ul>
</section>

</body>
</html>
```